2 x Digitize Logo | 2 x Business Cards | 2 x Fridge Magnets

We require 6 deliverables:
1. Residential logo redrawn (same just high quality for large print format).
2. Corporate logo redrawn (minor changes to wording and high quality for large print format).
3. New business card design for Furniture Removals (residential)
4. New business card design for Corporate Relocations (business)
5. New Fridge magnet for Furniture removals (residential)
6. New fridge magnet for Corporate Relocations (business)
1. Residential Logo
a. We require the logo to be translated into a high quality digital image with no modifications.
(see attached resilogo.jpg)
2. Residential Logo
a. We require the logo to be edited (add the word corporate relocations) be translated into a high quality digital image.
(see attached corplogo.jpg)
3. Using the resilogo please make a new business card for our business.
a. Please see the web site https://www.larkbendcarters.com.au for colours and inspiration.
b. The residential business card needs the following information:
i. Business Name (using the residential logo).
ii. Free Call: 1800 LB Cart (the L, B and Cart much be the same colour as the logo).
iii. Website: www.LarkbendCarters.com.au
iv. Address: 4/17 Ormsdale Court, VIC 3264
v. Email: cart@LarkbendCarters.com.au
vi. backof Card:
Review our service
www.PennantOrbit.com.au
Services: Local, Country, Interstate | Furniture Removals | Piano, Billiard Tables & Antiques
4. Using the corplogo please make a new business card for our business.
b. The corporate business card needs the following information:
i. Business Name (using the corporate logo).
v. Email: corporate@LarkbendCarters.com.au
vi. Back of Card:
Review our service
www.PennantOrbit.com.au
Services: Corporate relocations | Office equipment moves | Packing Service | Packing Materials
5. Using the resilogo please make a new fridge magent for our business.
b. The residential fidge magnet needs the following information:
iv. Services: Local, Country, Interstate | Furniture Removals | Piano, Billiard Tables & Antiques
6. Using the corplogo please make a new fridge magent for our business.
b. The corporate fidge magnet needs the following information:
iv. Services: Local, Country, Interstate | Corporate relocations
Target Market(s)
Residential Furniture Removals and Corporate Office relocations
Industry/Entity Type
Business
Contact Information for Business Card
Please see full brief for six items required
Requirements
Must have
- Clean simple, easy to read
Nice to have
- fresh, stand out, eye catching
Should not have
- plain, standard, boring, general

```html
<!DOCTYPE html>
<html lang="en">
<head>
<meta charset="utf-8">
<title>Larkbend Carters – Business Cards</title>
<link href="https://fonts.googleapis.com/css2?family=Oswald:wght@500;700&family=Roboto+Condensed:wght@400;500&family=Open+Sans:wght@400;600&display=swap" rel="stylesheet">
<style>
  :root{
    --page:#cbcbcb;
    --card:#2b2b2b;
    --white:#ffffff;
    --green:#0a9a47;
    --red:#e0241f;
    --yellow:#f2a900;
    --grey-line:#9a9a9a;
    --text:#f2f2f2;
  }
  *{margin:0;padding:0;box-sizing:border-box}
  html,body{width:1200px;height:782px;overflow:hidden;background:var(--page)}
  .sheet{position:relative;width:1200px;height:782px}
  .card{position:absolute;width:417px;height:251px;background:var(--card);overflow:hidden;
        box-shadow:8px 10px 14px rgba(0,0,0,.28)}
  .card--resi-back{left:165px;top:118px}
  .card--resi-front{left:617px;top:118px}
  .card--corp-back{left:165px;top:412px}
  .card--corp-front{left:617px;top:412px}
  .card svg.curve{position:absolute;inset:0}
  .abs{position:absolute}

  .brand{font-family:"Oswald",sans-serif;font-weight:700;letter-spacing:.5px;white-space:nowrap;text-transform:uppercase}
  .brand--back{left:0;right:0;text-align:center;font-size:32px;color:var(--yellow);top:56px;line-height:1}
  .brand--corp{left:0;right:0;text-align:center;font-size:24px;color:var(--red);top:70px;line-height:1}
  .tagline{font-family:"Open Sans",sans-serif;font-size:9.5px;color:var(--green);text-align:center;left:0;right:0;line-height:1;text-transform:uppercase}
  .tagline--back{top:99px}

  .review{left:0;right:0;top:139px;text-align:center;font-family:"Open Sans",sans-serif;font-size:11.5px;color:var(--text)}
  .review--corp{top:177px}
  .rule{position:absolute;top:147px;height:2px;width:88px;background:linear-gradient(90deg,transparent,var(--grey-line) 30%,var(--grey-line))}
  .rule--left{left:61px}
  .rule--right{left:267px;transform:scaleX(-1)}
  .rule--corp{top:185px}
  .review-url{left:0;right:0;top:156px;text-align:center;font-family:"Open Sans",sans-serif;font-size:15px;color:var(--text)}
  .review-url--corp{top:194px}
  .review-url b{font-weight:600}
  .y{color:var(--yellow)} .r{color:var(--red)} .g{color:var(--green)}
  .services{left:0;right:0;top:222px;text-align:center;font-family:"Roboto Condensed",sans-serif;font-weight:500;font-size:10.3px;color:var(--text);white-space:nowrap}
  .services .sep{color:var(--yellow);padding:0 4px}

  .person{left:18px;top:40px;font-family:"Oswald",sans-serif;font-weight:700;font-size:17px;color:var(--red);text-transform:uppercase;line-height:1}
  .role{left:18px;top:63px;font-family:"Roboto Condensed",sans-serif;font-size:9.5px;color:var(--text)}
  .contact{left:18px;top:165px;font-family:"Roboto Condensed",sans-serif;font-size:10px;color:var(--text);line-height:15px}
  .contact .address{margin-bottom:5px;font-size:10.5px}
  .contact li{list-style:none;display:flex;align-items:center;gap:7px;white-space:nowrap}
  .contact svg{width:9px;height:9px;flex:none}

  .brand--vertical{left:272px;top:127px;transform-origin:center;transform:translate(-50%,-50%) rotate(-90deg);
        font-size:30px;line-height:30px;color:var(--green);text-align:left}
  .front-corp-logo{left:200px;width:225px;top:104px;text-align:center}
  .front-corp-logo .brand{font-size:21px;color:var(--red);line-height:1}
  .front-corp-logo .tagline{position:static;margin-top:6px;font-size:9px}
</style>
</head>
<body>
<main class="sheet">

  <!-- Residential back -->
  <section class="card card--resi-back">
    <div class="abs brand brand--back">Larkbend Carters</div>
    <span class="rule rule--left"></span><span class="rule rule--right"></span>
    <p class="abs review">Review our service</p>
    <p class="abs review-url">www.<b class="y">Pennant</b><b class="g">Orbit</b>.com.au</p>
    <p class="abs services">Local, Country, Interstate<span class="sep">|</span>Furniture Removals<span class="sep">|</span>Piano, Billiard Tables &amp; Antiques</p>
  </section>

  <!-- Residential front -->
  <section class="card card--resi-front">
    <svg class="curve" viewBox="0 0 417 251" aria-hidden="true">
      <path d="M258 38 Q190 150 294 251 L306 251 Q205 150 266 30 Z" fill="var(--green)"/>
      <path d="M267 0 Q179 125 291 251 L417 251 L417 0 Z" fill="var(--white)"/>
    </svg>
    <div class="abs brand brand--vertical">Larkbend<br>Carters</div>
    <h2 class="abs person">Dana Whitlow</h2>
    <p class="abs role">Managing Director</p>
    <div class="abs contact">
      <p class="address">4/17 Ormsdale Court, VIC 3264</p>
      <ul>
        <li><svg viewBox="0 0 10 10"><path d="M1 4 Q5 0 9 4 L8 5 L6 4 L6 3 L4 3 L4 4 L2 5 Z M2 6 L8 6 L8 9 L2 9 Z" fill="var(--green)"/></svg>Free Call: 1800 LB Cart</li>
        <li><svg viewBox="0 0 10 10"><rect x="0.5" y="2" width="9" height="6.5" fill="var(--red)"/><path d="M0.5 2 L5 6 L9.5 2" stroke="var(--card)" fill="none"/></svg>cart@LarkbendCarters.com.au</li>
        <li><svg viewBox="0 0 10 10"><circle cx="5" cy="5" r="4.3" fill="none" stroke="var(--green)"/><path d="M0.7 5 H9.3 M5 0.7 V9.3" stroke="var(--green)"/><ellipse cx="5" cy="5" rx="2" ry="4.3" fill="none" stroke="var(--green)"/></svg>www.<span class="y">Larkbend</span><span class="r">Carters</span>.com.au</li>
      </ul>
    </div>
  </section>

  <!-- Corporate back -->
  <section class="card card--corp-back">
    <div class="abs brand brand--corp">Larkbend Carters</div>
    <p class="abs tagline tagline--back">Corporate Relocations</p>
    <span class="rule rule--left rule--corp"></span><span class="rule rule--right rule--corp"></span>
    <p class="abs review review--corp">Review our service</p>
    <p class="abs review-url review-url--corp">www.<b class="y">Pennant</b><b class="g">Orbit</b>.com.au</p>
    <p class="abs services">Corporate relocations<span class="sep">|</span>Office equipment moves<span class="sep">|</span>Packing Service<span class="sep">|</span>Packing Materials</p>
  </section>

  <!-- Corporate front -->
  <section class="card card--corp-front">
    <svg class="curve" viewBox="0 0 417 251" aria-hidden="true">
      <path d="M250 0 L266 0 Q150 95 238 251 L228 251 Q132 95 250 0 Z" fill="var(--green)"/>
      <path d="M274 0 Q151 90 251 251 L417 251 L417 0 Z" fill="var(--white)"/>
    </svg>
    <h2 class="abs person">Dana Whitlow</h2>
    <p class="abs role">Managing Director</p>
    <div class="abs front-corp-logo">
      <div class="brand">Larkbend Carters</div>
      <p class="tagline">Corporate Relocations</p>
    </div>
    <div class="abs contact">
      <p class="address">4/17 Ormsdale Court, VIC 3264</p>
      <ul>
        <li><svg viewBox="0 0 10 10"><path d="M1 4 Q5 0 9 4 L8 5 L6 4 L6 3 L4 3 L4 4 L2 5 Z M2 6 L8 6 L8 9 L2 9 Z" fill="var(--green)"/></svg>Free Call: 1800 LB Cart</li>
        <li><svg viewBox="0 0 10 10"><rect x="0.5" y="2" width="9" height="6.5" fill="var(--red)"/><path d="M0.5 2 L5 6 L9.5 2" stroke="var(--card)" fill="none"/></svg>corporate@LarkbendCarters.com.au</li>
        <li><svg viewBox="0 0 10 10"><circle cx="5" cy="5" r="4.3" fill="none" stroke="var(--green)"/><path d="M0.7 5 H9.3 M5 0.7 V9.3" stroke="var(--green)"/><ellipse cx="5" cy="5" rx="2" ry="4.3" fill="none" stroke="var(--green)"/></svg>www.<span class="y">Larkbend</span><span class="r">Carters</span>.com.au</li>
      </ul>
    </div>
  </section>

</main>
</body>
</html>
```